Business Card Design for a Personal Trainer

I need a business card design for my job as a personal trainer. It should have a unique, modern and exclusive design. On the front there should be only my logo with my name and my job. 0162/3819204 Tobias Lendhart Wiesengrundweg 14 80417 Munich Germany The most important contact information is the web adress. it can be bigger than the rest, but its not necessary. The card should be 8,5cmx5,5cm big. Font: Roboto. Colors: black, white, gray, 56c1ff.

```html
<!DOCTYPE html>
<html lang="de">
<head>
<meta charset="utf-8">
<title>Tobias Lendhart – Personal Trainer Visitenkarte</title>
<link href="https://fonts.googleapis.com/css2?family=Roboto:wght@300;400;500&display=swap" rel="stylesheet">
<style>
  :root {
    --stage: #2a2a2c;
    --card: #1c1d1f;
    --photo-light: #b4b4b4;
    --photo-dark: #4a4a4a;
    --text: #e9e9e9;
    --muted: #8a8a8a;
    --accent: #56c1ff;
    --white: #ffffff;
    --field-light: #3a3b3e;
    --field-mid: #27282a;
    --field-dark: #18191a;
  }
  * { margin: 0; padding: 0; box-sizing: border-box; }
  html, body {
    width: 1200px; height: 1108px; overflow: hidden;
    background: var(--stage);
    font-family: 'Roboto', sans-serif;
  }
  .cards {
    position: absolute; inset: 0;
    display: flex; justify-content: center; align-items: center; gap: 80px;
  }
  .card {
    width: 360px; height: 556px;
    border-radius: 22px;
    background: var(--card);
    position: relative;
    overflow: hidden;
    box-shadow: 0 18px 40px rgba(0,0,0,.45);
  }
  /* Contact side */
  .portrait {
    position: absolute; left: 36px; top: 36px;
    width: 288px; height: 292px;
    border-radius: 22px;
    background: linear-gradient(180deg, var(--photo-light) 0%, #9c9c9c 55%, var(--photo-dark) 100%);
  }
  .contact-divider {
    position: absolute; left: 40px; right: 40px; top: 354px;
    display: flex; align-items: center; gap: 6px;
  }
  .contact-divider .rule { flex: 1; height: 1px; background: var(--muted); }
  .contact-divider svg { display: block; }
  .contact-list {
    position: absolute; left: 0; right: 0; top: 380px;
    text-align: center; color: var(--text);
    font-weight: 400; line-height: 1.3;
  }
  .contact-list .phone, .contact-list .email { font-size: 17px; }
  .contact-list .web { font-size: 23px; color: var(--white); margin-top: 2px; }
  .contact-list .sep { width: 230px; height: 1px; background: var(--muted); margin: 6px auto 8px; }
  .contact-list .address { font-size: 17px; font-weight: 300; }
  /* Brand side */
  .card--brand { background: var(--field-dark); }
  .pattern-field {
    position: absolute; inset: 0;
    background:
      radial-gradient(ellipse at 25% 15%, rgba(255,255,255,.07) 0%, rgba(255,255,255,0) 60%),
      linear-gradient(160deg, var(--field-light) 0%, var(--field-mid) 50%, var(--field-dark) 100%);
  }
  .brand-lockup {
    position: absolute; left: 0; right: 0; bottom: 70px;
    text-align: center; color: var(--white);
  }
  .brand-mark {
    width: 72px; height: 72px; background: var(--white);
    margin: 0 auto 22px;
  }
  .brand-name {
    font-size: 35px; font-weight: 400; letter-spacing: 1px;
    text-transform: uppercase; line-height: 1.1;
  }
  .brand-role {
    display: flex; align-items: center; justify-content: center; gap: 10px;
    margin-top: 6px;
  }
  .brand-role .rule { width: 44px; height: 1px; background: var(--white); }
  .brand-role span {
    font-size: 14px; font-weight: 300; letter-spacing: 5px; text-transform: uppercase;
  }
</style>
</head>
<body>
<main class="cards">
  <section class="card card--contact">
    <div class="portrait" role="img" aria-label="Schwarz-weißes Porträtfoto des Trainers im Sportshirt"></div>
    <div class="contact-divider">
      <span class="rule"></span>
      <svg width="74" height="22" viewBox="0 0 74 22" aria-hidden="true">
        <circle cx="11" cy="11" r="10" fill="var(--accent)"/>
        <path d="M7 6.5c0 5 3.5 8.5 8.5 8.5l1-2-2.5-1-1 1c-1.5-.6-2.7-1.8-3.3-3.3l1-1-1-2.5z" fill="#1c1d1f"/>
        <circle cx="37" cy="11" r="10" fill="var(--accent)"/>
        <rect x="31" y="7" width="12" height="8" fill="#1c1d1f"/>
        <path d="M31 7l6 4.5 6-4.5" stroke="var(--accent)" stroke-width="1" fill="none"/>
        <circle cx="63" cy="11" r="10" fill="var(--accent)"/>
        <circle cx="63" cy="11" r="5.5" fill="none" stroke="#1c1d1f" stroke-width="1.4"/>
        <path d="M57.5 11h11M63 5.5c-2.5 3-2.5 8 0 11M63 5.5c2.5 3 2.5 8 0 11" stroke="#1c1d1f" stroke-width="1.1" fill="none"/>
      </svg>
      <span class="rule"></span>
    </div>
    <div class="contact-list">
      <p class="phone">0162/3819204</p>
      <p class="email">t.lendhart@mailpost.de</p>
      <p class="web">www.tobiaslendhart.de</p>
      <div class="sep"></div>
      <p class="address">Wiesengrundweg 14<br>80417 München</p>
    </div>
  </section>

  <section class="card card--brand">
    <div class="pattern-field" role="img" aria-label="Dezentes dunkles Muster aus wiederholten Markenzeichen über die ganze Kartenfläche"></div>
    <div class="brand-lockup">
      <div class="brand-mark"></div>
      <p class="brand-name">Tobias Lendhart</p>
      <div class="brand-role"><span class="rule"></span><span>Personal Trainer</span><span class="rule"></span></div>
    </div>
  </section>
</main>
</body>
</html>
```